Quorva - corporate Business Card

We need a good look and innovative business card for a new start up company based in Los Angeles called "Quorva". We are in a payment business, including payment card, app, and ewallet. We are expert in online payment and Card not present (CNP) transaction.
We need an innovative, modern business card.

Our logo font is Aero Matics

Target Market(s)

Startup - Bank - Online Payment - Card Manufacturing

Industry/Entity Type

Startup

Contact Information for Business Card

phone: 555 014 7396 - Address: 4172 Marlowe blvd, Tessaly Park, OR 97299

Requirements
Must have
• Message: innovative, professional, expert, high tech, trust, online payment expert, security
Nice to have
• no comment
Should not have
• no Comment

```html
<!DOCTYPE html>
<html lang="en">
<head>
<meta charset="utf-8">
<title>Quorva – Business Card</title>
<link rel="stylesheet" href="https://fonts.googleapis.com/css2?family=Play:wght@400;700&display=swap">
<style>
  :root {
    --backdrop: #808080;
    --card-light: #f8f8f8;
    --card-dark: #060102;
    --brand-red: #b51e2e;
    --ink: #111111;
    --white: #ffffff;
    --disc-top: #fafafa;
    --disc-bottom: #dcdcdc;
  }
  * { box-sizing: border-box; margin: 0; padding: 0; }
  html, body { width: 1200px; height: 900px; overflow: hidden; }
  body {
    background: var(--backdrop);
    font-family: "Play", "Arial", sans-serif;
    position: relative;
  }
  .card {
    position: absolute;
    top: 271px;
    width: 457px;
    height: 282px;
    border-radius: 14px;
  }
  .card--front { left: 137px; background: var(--card-light); }
  .card--back { left: 626px; background: var(--card-dark); }

  .brand-disc {
    position: absolute;
    border-radius: 50%;
    display: flex;
    align-items: center;
    justify-content: center;
    font-weight: 700;
  }
  .card--front .brand-disc {
    left: 57px; top: 59px; width: 164px; height: 164px;
    background: var(--brand-red);
    color: var(--white);
    font-size: 30px;
  }
  .card--back .brand-disc {
    left: 156px; top: 67px; width: 146px; height: 146px;
    background: linear-gradient(180deg, var(--disc-top), var(--disc-bottom));
    color: var(--card-dark);
    font-size: 27px;
  }

  .details { position: absolute; left: 255px; top: 59px; color: var(--ink); }
  .details__name { color: var(--brand-red); font-size: 22px; font-weight: 700; line-height: 26px; }
  .details__role { font-size: 15px; line-height: 18px; }
  .contact-list { list-style: none; margin-top: 20px; }
  .contact-list li {
    display: flex; align-items: center; gap: 8px;
    font-size: 14.5px; line-height: 21px;
  }
  .contact-list svg { width: 18px; height: 18px; flex: none; }
  .details__address { margin-top: 19px; font-size: 13.5px; line-height: 17px; }
</style>
</head>
<body>
  <section class="card card--front" aria-label="Business card front">
    <div class="brand-disc">Quorva</div>
    <div class="details">
      <p class="details__name">Dale Corwin</p>
      <p class="details__role">Director</p>
      <ul class="contact-list">
        <li>
          <svg viewBox="0 0 18 18" aria-hidden="true">
            <circle cx="9" cy="9" r="9" fill="var(--brand-red)"/>
            <rect x="6" y="3.5" width="6" height="11" rx="1.2" fill="none" stroke="#fff" stroke-width="1.4"/>
            <circle cx="9" cy="12.3" r="0.8" fill="#fff"/>
          </svg>
          555 014 7396
        </li>
        <li>
          <svg viewBox="0 0 18 18" aria-hidden="true">
            <circle cx="9" cy="9" r="9" fill="var(--brand-red)"/>
            <circle cx="9" cy="9" r="5" fill="none" stroke="#fff" stroke-width="1.4"/>
            <path d="M4 9h10M9 4c-2 3-2 7 0 10M9 4c2 3 2 7 0 10" fill="none" stroke="#fff" stroke-width="1"/>
          </svg>
          www.quorva.com
        </li>
      </ul>
      <p class="details__address">4172 Marlowe blvd,<br>Tessaly Park, OR 97299</p>
    </div>
  </section>

  <section class="card card--back" aria-label="Business card back">
    <div class="brand-disc">Quorva</div>
  </section>
</body>
</html>
```